Website Design for The Elder Nook

Please design and code a new website.
Here are the sites I like best:
http://www.voyaglint.com/alternate/
http://www.wheelgiftbay.org
Please make it similar but look at the competitor site (below) for images and wording. This is NOT a car donation site. It's a senior lead placement site like https://www.kinhavenfinder.com. I just like this sites above as a lead generation sites.
Competitor site:
https://www.kinhavenfinder.com (use ideas / verbiage from this site)
Updates
Competitor site:
Coding
Coded - Design and coding required
Number of Pages Required
1 page
Look and feel
Each slider illustrates characteristics of the customer's brand and the style your logo design should communicate.

```html
<!DOCTYPE html>
<html lang="en">
<head>
<meta charset="utf-8">
<title>The Elder Nook – Senior Living Advice</title>
<link rel="stylesheet" href="https://fonts.googleapis.com/css2?family=Lato:ital,wght@0,400;0,700;1,400&family=Noticia+Text:ital,wght@0,400;0,700;1,400;1,700&family=Oswald:wght@400;500&display=swap">
<style>
:root{
  --navy:#0d2a4e;
  --green:#8cc63f;
  --blue:#1859a8;
  --text:#333b45;
  --muted:#6b7380;
  --line:#dfe3e8;
  --white:#fff;
}
*{box-sizing:border-box;margin:0;padding:0}
html,body{width:1200px;height:3316px;overflow:hidden}
body{position:relative;background:var(--white);font-family:"Lato",sans-serif;color:var(--text)}
.abs{position:absolute}
.serif{font-family:"Noticia Text",serif}
.accent{color:var(--green);font-style:italic;font-weight:700}

/* header */
.header{top:0;left:0;width:1200px;height:91px}
.brand{left:80px;top:24px;display:flex;align-items:center;gap:12px;font-family:"Noticia Text",serif;font-size:32px;color:var(--navy)}
.brand-mark{width:26px;height:26px;background:var(--green);border-radius:50%}
.call{left:704px;top:22px;display:flex;gap:14px;align-items:center}
.call small{display:block;font-size:10px;color:var(--muted)}
.call strong{font-family:"Oswald",sans-serif;font-weight:400;font-size:24px;color:var(--navy);letter-spacing:.5px}
.badge{left:920px;top:19px;width:128px;height:48px;background:var(--navy);border-radius:4px}
.lang{left:1081px;top:36px;display:flex;gap:4px;align-items:center}
.lang i{width:16px;height:16px;border-radius:50%;background:linear-gradient(#c33 0 50%,#2a4a8c 50%)}

.nav{left:0;width:1200px;height:49px;background:var(--navy);display:flex;justify-content:center;align-items:center}
.nav a{font-family:"Oswald",sans-serif;color:#fff;text-decoration:none;font-size:15.5px;text-transform:uppercase;height:49px;line-height:49px;padding:0 26px}
.nav a.on{background:var(--green)}
.top-nav{top:91px;padding-left:16px}
.top-nav a.on{padding:0 26px;margin-right:24px}

/* hero */
.hero{top:140px;left:0;width:1200px;height:541px;background:linear-gradient(180deg,#8fb6da 0%,#c9dceb 40%,#d9cfc0 62%,#c6b59d 100%)}
.hero-people{left:0;top:0;width:420px;height:541px;background:linear-gradient(180deg,rgba(40,60,100,.25),rgba(150,130,110,.3))}
.tagline{left:400px;top:237px;width:380px;text-align:center;font-family:"Noticia Text",serif;font-size:29px;line-height:42px;color:#1f2a36}
.inquiry{left:783px;top:70px;width:328px;height:420px;background:#fff;box-shadow:0 10px 20px rgba(0,0,0,.15);padding:10px}
.inquiry h2{background:var(--green);color:#fff;font-family:"Noticia Text",serif;font-weight:400;font-size:25px;text-align:center;height:72px;line-height:60px;clip-path:polygon(0 0,100% 0,100% 78%,50% 100%,0 78%)}
.field{display:flex;border:1px solid var(--line);height:41px;margin-top:12px;border-radius:2px;font-size:13px;color:var(--muted)}
.field .ic{width:40px;border-right:1px solid var(--line);display:flex;align-items:center;justify-content:center}
.field .ic b{width:10px;height:10px;background:#555;border-radius:2px}
.field span{padding:12px 16px}
.field.msg{height:70px}
.inquiry .submit{margin-top:18px;height:38px;background:var(--blue);color:#fff;font-family:"Noticia Text",serif;font-size:15px;text-align:center;line-height:38px;border-radius:2px}

/* support */
.support-photo{left:142px;top:773px;width:422px;height:387px;background:linear-gradient(180deg,#4f8fd4 0%,#9cc3e8 45%,#7d7f7a 100%)}
.support{left:615px;top:770px;width:460px}
.support h2{font-family:"Noticia Text",serif;font-weight:400;font-size:28px;line-height:42px;color:var(--navy)}
.support p{font-size:13.5px;line-height:24px;margin:12px 0 14px;color:var(--text)}
.support ul{list-style:none}
.support li{display:flex;align-items:center;gap:14px;height:48px;font-size:13.5px}
.support li i{width:34px;height:34px;border-radius:50%;background:var(--blue);position:relative}
.support li i::after{content:"";position:absolute;left:11px;top:11px;width:12px;height:12px;border:2px solid #fff;border-radius:2px}
.support li i.g{background:var(--green)}

.nocost{left:142px;top:1232px;width:916px;height:174px;background:#fff;border:1px solid #eef1e8;box-shadow:0 8px 20px rgba(140,198,63,.18);text-align:center;padding-top:36px}
.nocost h2{font-family:"Noticia Text",serif;font-style:italic;font-weight:700;font-size:31px;color:var(--navy)}
.nocost p{font-style:italic;font-size:16.5px;margin:10px 0 6px}
.nocost .cta{font-family:"Oswald",sans-serif;font-size:32px;color:var(--blue);font-weight:500}
.nocost .cta span{color:var(--green);font-weight:400}

/* advisor */
.advisor{top:1510px;left:0;width:1200px;height:495px;background:linear-gradient(90deg,#1d3256 0%,#2c4266 40%,#1b2e52 100%)}
.advisor-photo{left:150px;top:20px;width:300px;height:475px;background:linear-gradient(180deg,rgba(110,130,160,.5),rgba(40,60,90,.4))}
.advisor-card{left:424px;top:57px;width:634px;height:388px;background:#fff;text-align:center;padding-top:40px}
.advisor-card h2{font-family:"Noticia Text",serif;font-style:italic;font-weight:400;font-size:28px;color:var(--navy)}
.advisor-card p.lead{font-size:13.5px;margin-top:14px}
.perks{display:flex;justify-content:space-around;padding:36px 30px 0}
.perks div{width:160px;font-size:13.5px;line-height:18px}
.perks svg{display:block;margin:0 auto 14px}
.finder{display:flex;margin:34px 42px 0;border:1px solid var(--line);height:46px}
.finder span{flex:1;text-align:left;padding:14px 18px;font-size:13.5px;color:#555}
.finder b{width:250px;background:var(--green);color:#fff;font-family:"Noticia Text",serif;font-size:15px;line-height:44px}

/* reviews */
.reviews-title{left:0;top:2078px;width:1200px;text-align:center;font-family:"Noticia Text",serif;font-size:29px;color:var(--navy)}
.card{top:2167px;width:436px;height:203px;border:1px solid var(--line);padding:32px 24px}
.card .who{display:flex;gap:16px;align-items:center}
.card .av{width:54px;height:54px;border-radius:50%;background:#e4ebf2;border:2px solid var(--green)}
.card h3{font-family:"Noticia Text",serif;font-size:15px;color:var(--navy)}
.card .stars{color:#f26a21;font-size:11px;letter-spacing:3px}
.card .q{position:absolute;right:22px;top:36px;font-family:"Noticia Text",serif;font-size:80px;line-height:60px;color:#dff0c8}
.card p{font-size:12.5px;line-height:23px;margin-top:18px;color:#444}
.arrow{top:2250px}

/* veterans */
.vets{top:2450px;left:0;width:1200px;height:317px;background:linear-gradient(90deg,#1c3466 0%,#25355f 47%,#2a2c55 100%);text-align:center;color:#fff;padding-top:72px}
.vets h2{font-family:"Noticia Text",serif;font-style:italic;font-weight:700;font-size:34px}
.vets p{font-size:16px;line-height:28px;margin:10px auto 0;width:900px}
.vets .btn{display:inline-block;margin-top:22px;background:var(--green);font-family:"Noticia Text",serif;font-weight:700;font-size:14px;width:130px;height:38px;line-height:38px}

/* states */
.states-title{left:0;top:2862px;width:1200px;text-align:center;font-family:"Noticia Text",serif;font-size:29px;color:var(--navy)}
.states{top:2928px;list-style:none;font-size:12.5px}
.states li{height:25.4px;line-height:25.4px}
.states li::before{content:"›";color:var(--green);margin-right:8px}

/* footer */
.foot-nav{top:3202px;height:76px}
.foot-nav a{height:76px;line-height:76px;padding:0 17px}
.copy{top:3278px;left:0;width:1200px;height:38px;background:var(--green);font-size:12px;color:var(--navy)}
.copy span{position:absolute;left:143px;top:12px}
.social{position:absolute;left:945px;top:8px;display:flex;gap:6px}
.social i{width:24px;height:24px;border-radius:50%;background:var(--navy)}
</style>
</head>
<body>

<header class="abs header">
  <div class="abs brand"><span class="brand-mark"></span>The Elder Nook</div>
  <div class="abs call">
    <svg width="28" height="28" viewBox="0 0 24 24" fill="none" stroke="#1859a8" stroke-width="1.6"><path d="M5 3h4l2 5-3 2a12 12 0 0 0 6 6l2-3 5 2v4a2 2 0 0 1-2 2A17 17 0 0 1 3 5a2 2 0 0 1 2-2z"/></svg>
    <div><small>Talk to a local advisor for FREE</small><strong>(555) 014-2288</strong></div>
  </div>
  <div class="abs badge" role="img" aria-label="Accreditation badge"></div>
  <div class="abs lang"><i></i><svg width="8" height="6" viewBox="0 0 8 6"><path d="M1 1l3 3 3-3" stroke="#333" fill="none"/></svg></div>
</header>

<nav class="abs nav top-nav">
  <a class="on" href="#">Assisted Living</a>
  <a href="#">Memory Care</a>
  <a href="#">Nursing Homes</a>
  <a href="#">More Living Options ⌄</a>
  <a href="#">Planning &amp; Advice</a>
  <a href="#">How Our Service Works</a>
</nav>

<section class="abs hero">
  <div class="abs hero-people" role="img" aria-label="Smiling senior couple piggybacking on a sunny beach"></div>
  <p class="abs tagline">You know your family.<br>We know <i>Senior Living.</i></p>
  <form class="abs inquiry">
    <h2>Quick Inquiry</h2>
    <div class="field"><div class="ic"><b></b></div><span>Name</span></div>
    <div class="field"><div class="ic"><b></b></div><span>Phone</span></div>
    <div class="field"><div class="ic"><b></b></div><span>Email</span></div>
    <div class="field msg"><div class="ic"><b></b></div><span>Message</span></div>
    <div class="submit">Submit Now</div>
  </form>
</section>

<div class="abs support-photo" role="img" aria-label="Group of cheerful seniors with bicycles waving under a blue sky"></div>
<section class="abs support">
  <h2>The support you need to make the<br><span class="accent">Right Choice</span></h2>
  <p>Lorem ipsum dolor sit amet, consectetuer adipiscing elit, sed nonummy nibh euismod tincidunt ut laoreet dolore magna aliquam erat</p>
  <ul>
    <li><i></i>Dedicated local advisor</li>
    <li><i></i>Hand-picked list of communities to match your needs</li>
    <li><i class="g"></i>Full details &amp; pricing</li>
    <li><i></i>Help scheduling tours</li>
    <li><i></i>Move in support</li>
  </ul>
</section>

<section class="abs nocost">
  <h2>There's No Cost To You</h2>
  <p>We work with over 20,000 senior living communities. Our community partners pay us for placement services.</p>
  <div class="cta">CALL <span>555-010-4471</span></div>
</section>

<section class="abs advisor">
  <div class="abs advisor-photo" role="img" aria-label="Smiling local advisor in a suit"></div>
  <div class="abs advisor-card">
    <h2>Your <span class="accent">Local Advisor</span> Informs. You Decide.</h2>
    <p class="lead">Over 400 senior advisors across the U.S. and Canada are ready to help your family with:</p>
    <div class="perks">
      <div><svg width="34" height="44" viewBox="0 0 34 44" fill="none" stroke="#8cc63f" stroke-width="1.6"><path d="M17 42S3 26 3 16a14 14 0 0 1 28 0c0 10-14 26-14 26z"/><circle cx="17" cy="16" r="4"/></svg>Insider's tips for the area near you</div>
      <div><svg width="46" height="42" viewBox="0 0 46 42" fill="none" stroke="#8cc63f" stroke-width="1.6"><path d="M23 40S2 26 2 13A10 10 0 0 1 23 8a10 10 0 0 1 21 5c0 13-21 27-21 27z"/></svg>Advice tailored to your unique situation</div>
      <div><svg width="44" height="40" viewBox="0 0 44 40" fill="none" stroke="#8cc63f" stroke-width="1.6"><circle cx="4" cy="5" r="3"/><circle cx="4" cy="20" r="3"/><circle cx="4" cy="35" r="3"/><path d="M14 5h28M14 20h28M14 35h28"/></svg>Time saving know-how and resources</div>
    </div>
    <div class="finder"><span>Enter city or postal code</span><b>Find An Advisor Near You</b></div>
  </div>
</section>

<h2 class="abs reviews-title">93% Of Our <span class="accent">Customers Recommend</span> Our Service</h2>
<svg class="abs arrow" style="left:88px" width="24" height="42" viewBox="0 0 24 42"><path d="M20 2L3 21l17 19" fill="none" stroke="#1859a8" stroke-width="1.6"/></svg>
<svg class="abs arrow" style="left:1088px" width="24" height="42" viewBox="0 0 24 42"><path d="M4 2l17 19L4 40" fill="none" stroke="#8cc63f" stroke-width="1.6"/></svg>
<article class="abs card" style="left:142px">
  <div class="who"><div class="av" role="img" aria-label="Reviewer portrait"></div><div><h3>Marla Quinn</h3><div class="stars">★★★★★</div></div></div>
  <span class="q">“</span>
  <p>Lorem ipsum dolor sit amet, consectetuer adipiscing elit, sed diam nonummy nibh euismod tincidunt ut laoreet dolore magna aliquam erat volutpat. Ut wisi enim ad minim veniam, quis</p>
</article>
<article class="abs card" style="left:622px">
  <div class="who"><div class="av" role="img" aria-label="Reviewer portrait"></div><div><h3>Devon Ashby</h3><div class="stars">★★★★★</div></div></div>
  <span class="q">“</span>
  <p>Lorem ipsum dolor sit amet, consectetuer adipiscing elit, sed diam nonummy nibh euismod tincidunt ut laoreet dolore magna aliquam erat volutpat. Ut wisi enim ad minim veniam, quis</p>
</article>

<section class="abs vets" aria-label="Waving flag background">
  <h2>Access Up To <span class="accent">$2,000 Per Month</span> In Veteran's Aid</h2>
  <p>We work with Veterans every day. Most veteran families do not know of a key benefit available to them &amp; their families. It's called the Veteran's Aid &amp; Attendance benefit. This benefit can help pay for senior living &amp; home care.</p>
  <span class="btn">Learn More</span>
</section>

<h2 class="abs states-title">Senior Assisted <span class="accent">Living by State</span></h2>
<ul class="abs states" style="left:142px"><li>Alabama</li><li>Arizona</li><li>Arkansas</li><li>California</li><li>Colorado</li><li>Connecticut</li><li>Delaware</li></ul>
<ul class="abs states" style="left:288px"><li>District of Columbia</li><li>Florida</li><li>Georgia</li><li>Hawaii</li><li>Idaho</li><li>Illinois</li><li>Indiana</li></ul>
<ul class="abs states" style="left:479px"><li>Iowa</li><li>Kansas</li><li>Kentucky</li><li>Louisiana</li><li>Maine</li><li>Maryland</li><li>Massachusetts</li></ul>
<ul class="abs states" style="left:640px"><li>Michigan</li><li>Minnesota</li><li>Mississippi</li><li>Missouri</li><li>Montana</li><li>Nebraska</li><li>Nevada</li></ul>
<ul class="abs states" style="left:780px"><li>New Hampshire</li><li>New Jersey</li><li>New Mexico</li><li>New York</li><li>North Carolina</li><li>North Dakota</li><li>Ohio</li></ul>
<ul class="abs states" style="left:949px"><li>Oklahoma</li><li>Oregon</li><li>Pennsylvania</li><li>Rhode Island</li><li>South Carolina</li><li>South Dakota</li><li>Tennessee</li></ul>

<nav class="abs nav foot-nav">
  <a href="#">Assisted Living</a>
  <a href="#">Memory Care</a>
  <a href="#">Nursing Homes</a>
  <a href="#">More Living Options ⌄</a>
  <a href="#">Planning &amp; Advice</a>
  <a href="#">How Our Service Works</a>
</nav>
<footer class="abs copy">
  <span>Copyright 2019 The Elder Nook. All Rights Reserved.</span>
  <div class="social"><i></i><i></i><i></i><i></i></div>
</footer>

</body>
</html>
```